Business Card (double-sided) and Stationary Design for dental office

1) Business Card Design: We need a business card design for a dental specialty office.
Texts should contain:
The name of our office "Brindle Oaks Orthodontics"
Tagline: "Specialist in Orthodontic and Maxillofacial Orthopedics"
Tag line: "Creating "Tolvering" smiles for Children and Adults"
Doctor name: "Doctor Name"
Office Address:
"123 Street Name
City, State Zip code"
Office email address: office@brindleoaksortho.com
Website: www.brindleoaksortho.com

We will provide the full office address once the design is selected
Theme: beach, paradise, coastal, wave
We would like to have some creativity in design. Some acceptable ideas: front page: logo and office name. Back page: more detail information, and map to office in form of an island. Please see sample from our other location, but you DON'T HAVE TO USE OR COPY THE SAME CONCEPT.

IF POSSIBLE, PLEASE SUBMIT AT LEAST TWO CONCEPTS: ONE WITH THE BACK LOOKING SIMILAR TO WHAT IS IN THE SAMPLE, AND ONE DIFFERENT.

Color: designer to choose. We have different shade of blues and sand color in our office. Please see logo.

2) Please also design a matching set of stationary that compliment the business card and our logo.

Target Market(s)

Dental

Contact Information for Business Card

See descriptions

Font styles to use
Other font styles liked:
• Matching texts in logo

Colors
0054AA
0677BA
7BADD7
CADEEF
E8F1F8
0094D4
00A9DD
6FCCEA
C7EBF8
E9F6FB
00AB8E
00BBA5
67D7C9
C6EFE9
E9F9F6

Requirements
Must have
• Double-sided
Nice to have
• Beach coastal theme
Should not have
• Any shape or drawing of of tooth or teeth. We don’t need these. You don't necessarily have to just cut and paste the logo art and text as a whole, you have the liberty to rearrange the text.

```html
<!DOCTYPE html>
<html lang="en">
<head>
<meta charset="utf-8">
<title>Brindle Oaks Orthodontics – Business Card</title>
<link rel="stylesheet" href="https://fonts.googleapis.com/css2?family=Raleway:wght@400;500;600;700&display=swap">
<style>
  :root {
    --stage: #2a2a2c;
    --card-dark: #0c0c0d;
    --card-light: #f7f8f8;
    --brand-blue: #3a8fab;
    --brand-mint: #7fd0bf;
    --ink-white: #f2f2f2;
    --ink-grey: #9aa3a5;
    --ink-dark: #444;
    --rule: #c9cfd0;
  }
  * { box-sizing: border-box; margin: 0; padding: 0; }
  html, body { width: 1200px; height: 900px; overflow: hidden; }
  body {
    background: var(--stage);
    font-family: "Raleway", sans-serif;
    display: flex;
    flex-direction: column;
    align-items: center;
    justify-content: center;
    gap: 56px;
  }
  .card {
    position: relative;
    width: 640px;
    height: 366px;
    border-radius: 26px;
    overflow: hidden;
    box-shadow: 0 12px 30px rgba(0,0,0,.45);
  }

  /* Front */
  .card-front { background: var(--card-dark); color: var(--ink-white); }
  .brand {
    position: absolute;
    left: 46px; top: 78px;
    width: 230px;
    display: flex; flex-direction: column; align-items: center; gap: 16px;
  }
  .brand-dot { width: 74px; height: 74px; border-radius: 50%; background: var(--brand-blue); }
  .brand-name {
    font-weight: 700; font-size: 24px; color: var(--brand-blue);
    text-align: center; line-height: 1.15;
  }
  .divider {
    position: absolute; left: 300px; top: 40px;
    width: 1px; height: 200px; background: #2c2c2e;
  }
  .contact { position: absolute; left: 330px; top: 52px; }
  .contact-name { font-weight: 700; font-size: 24px; color: var(--brand-blue); }
  .contact-role { font-weight: 500; font-size: 15px; margin-top: 2px; }
  .contact-address { font-size: 15px; line-height: 1.35; margin-top: 18px; }
  .contact-lines { list-style: none; margin-top: 18px; font-size: 15px; line-height: 1.5; }
  .contact-lines li { display: flex; align-items: center; gap: 8px; }
  .contact-lines svg { width: 14px; height: 14px; flex: none; }
  .band {
    position: absolute; left: 0; right: 0;
    top: 262px; height: 52px;
    display: flex; align-items: center; justify-content: center;
    color: #fff; font-weight: 600;
  }
  .band-front { background: var(--brand-blue); font-size: 19px; }

  /* Back */
  .card-back { background: var(--card-light); }
  .appt-title {
    position: absolute; left: 190px; top: 38px;
    font-weight: 600; font-size: 32px; color: var(--brand-blue);
  }
  .field {
    position: absolute;
    border-bottom: 1px solid var(--rule);
    color: var(--ink-grey); font-size: 20px; font-weight: 500;
    padding-bottom: 4px;
  }
  .field-name { left: 60px; top: 116px; width: 530px; }
  .field-date { left: 60px; top: 176px; width: 250px; }
  .field-time { left: 330px; top: 176px; width: 260px; display: flex; justify-content: space-between; }
  .notice {
    position: absolute; left: 0; right: 0; top: 232px;
    text-align: center; font-size: 12px; color: var(--ink-dark);
  }
  .band-back { background: var(--brand-mint); font-size: 16px; top: 262px; height: 44px; }
</style>
</head>
<body>

  <section class="card card-front" aria-label="Business card front">
    <div class="brand">
      <span class="brand-dot"></span>
      <span class="brand-name">Brindle Oaks Orthodontics</span>
    </div>
    <div class="divider"></div>
    <div class="contact">
      <p class="contact-name">Marcus Hale</p>
      <p class="contact-role">Managing Director</p>
      <p class="contact-address">123 Street Name<br>City, State Zip code</p>
      <ul class="contact-lines">
        <li>
          <svg viewBox="0 0 14 14"><rect x="1" y="3" width="12" height="8" fill="none" stroke="#3a8fab" stroke-width="1.4"/><path d="M1 3 L7 8 L13 3" fill="none" stroke="#3a8fab" stroke-width="1.4"/></svg>
          office@brindleoaksortho.com
        </li>
        <li>
          <svg viewBox="0 0 14 14"><circle cx="7" cy="7" r="5.8" fill="none" stroke="#3a8fab" stroke-width="1.3"/><ellipse cx="7" cy="7" rx="2.5" ry="5.8" fill="none" stroke="#3a8fab" stroke-width="1.1"/><path d="M1.2 7 H12.8" stroke="#3a8fab" stroke-width="1.1"/></svg>
          www.brindleoaksortho.com
        </li>
      </ul>
    </div>
    <div class="band band-front">Specialist in Orthodontic and Maxillofacial Orthopedics</div>
  </section>

  <section class="card card-back" aria-label="Business card back">
    <h2 class="appt-title">Next Appointment</h2>
    <div class="field field-name">Name</div>
    <div class="field field-date">Date</div>
    <div class="field field-time"><span>Time</span><span>am/ pm</span></div>
    <p class="notice">If you unable to keep appointment, please give 24 hours notice</p>
    <div class="band band-back">Creating Tolvering smiles for Children and Adults</div>
  </section>

</body>
</html>
```